Report Design

I am looking for a redesign of our monthly inspection reports we submit to our customers. I uploaded the current one we use (FernHollows) and also that of a competitor (Tall Ridge). I want to more copy the layout of the Tallridge report I attached but with more flow and design.

Requirements
Must have
• This has to be in a template format that we can modify the content every month.

```html
<!DOCTYPE html>
<html lang="en">
<head>
<meta charset="utf-8">
<title>Landscape Inspection Report Template</title>
<link href="https://fonts.googleapis.com/css2?family=Roboto:ital,wght@0,400;0,700;1,400;1,700&family=Open+Sans:ital,wght@1,600&display=swap" rel="stylesheet">
<style>
  :root {
    --brand-green: #21a038;
    --ink: #111111;
    --paper: #ffffff;
    --backdrop: #cccccc;
    --rule: #222222;
  }
  * { box-sizing: border-box; margin: 0; padding: 0; }
  html, body { width: 957px; height: 1200px; overflow: hidden; background: var(--backdrop); }
  .sheet-board { position: relative; width: 1720px; height: 2156px; transform: scale(0.5564); transform-origin: 0 0; }
  .page { position: absolute; width: 773px; height: 1000px; background: var(--paper); overflow: hidden; font-family: "Roboto", Arial, sans-serif; color: var(--ink); }
  .page--1 { left: 52px; top: 40px; }
  .page--2 { left: 903px; top: 40px; }
  .page--3 { left: 52px; top: 1107px; }
  .page--4 { left: 903px; top: 1107px; }

  .page-header { position: absolute; left: 0; top: 0; width: 773px; height: 215px; }
  .header-wave { position: absolute; left: 0; top: 0; }
  .brand-box { position: absolute; left: 48px; top: 30px; width: 171px; height: 84px; background: var(--paper); display: flex; align-items: center; justify-content: center; }
  .brand-name { font-family: "Roboto", Arial, sans-serif; font-weight: 700; font-size: 27px; color: var(--brand-green); letter-spacing: -0.5px; }
  .brand-tagline { position: absolute; left: 48px; top: 121px; font-size: 10.5px; font-weight: 700; color: var(--paper); font-family: Arial, "Roboto", sans-serif; }
  .report-kind { position: absolute; left: 262px; top: 38px; font-family: "Open Sans", Arial, sans-serif; font-style: italic; font-weight: 600; font-size: 27.5px; color: var(--paper); white-space: nowrap; }

  .property-title { position: absolute; left: 0; width: 773px; text-align: center; font-weight: 700; font-size: 28px; letter-spacing: 0.2px; }
  .page--1 .property-title { top: 198px; left: -12px; }
  .page--2 .property-title { top: 206px; }
  .page--3 .property-title, .page--4 .property-title { top: 206px; left: -8px; }
  .report-month { position: absolute; top: 232px; left: -12px; width: 773px; text-align: center; font-style: italic; font-weight: 700; font-size: 22px; }

  .inspection-table { position: absolute; left: 48px; width: 680px; border: 1.5px solid var(--rule); }
  .page--1 .inspection-table { top: 268px; }
  .page--2 .inspection-table { left: 53px; top: 258px; }
  .page--3 .inspection-table { top: 260px; }
  .page--4 .inspection-table { top: 260px; }
  .inspection-row { display: flex; height: 214px; border-top: 1.5px solid var(--rule); }
  .inspection-row:first-child { border-top: none; }
  .finding { width: 336px; border-right: 1.5px solid var(--rule); padding: 17px 12px 0 23px; }
  .finding-title { font-style: italic; font-weight: 700; font-size: 17.5px; margin-bottom: 5px; }
  .finding-text { font-size: 15px; line-height: 18.3px; max-width: 292px; }
  .page--2 .finding { padding-left: 26px; }
  .page--2 .finding-text { max-width: 266px; }
  .page--3 .finding-text { max-width: 270px; }
  .page--3 .finding-text--short { max-width: 248px; }
  .page--4 .finding-text { max-width: 300px; }
  .finding-title--tight { margin-bottom: 0; }

  .evidence { flex: 1; position: relative; }
  .photo { position: absolute; top: 0; height: 100%; }
  .photo--main { left: 70px; width: 212px; }
  .photo--short { top: 38px; height: 136px; left: 70px; width: 212px; }
  .photo--pair-a { left: 16px; width: 160px; }
  .photo--pair-b { left: 188px; width: 144px; }
  .photo--narrow { left: 103px; width: 161px; }

  .tone-grass { background: linear-gradient(180deg, #c8d3dc 0%, #b7a59e 40%, #b06e8a 60%, #5f8a3a 85%, #8a8a88 100%); }
  .tone-street { background: linear-gradient(180deg, #b9c4cc 0%, #4c5148 40%, #6b6d6c 60%, #4d6e2e 80%, #8b6b5a 100%); }
  .tone-wall { background: linear-gradient(180deg, #d8d4c8 0%, #c9c3b6 50%, #6b6a3c 75%, #8a8985 100%); }
  .tone-palm { background: linear-gradient(180deg, #dfe3e8 0%, #4f6f3a 30%, #7b8a5e 55%, #6d6e70 80%, #9a8776 100%); }
  .tone-shrub { background: linear-gradient(180deg, #d7dee5 0%, #88a07a 35%, #6d7161 55%, #3e6a2a 80%, #5a4a3c 100%); }
  .tone-red { background: linear-gradient(180deg, #d8dde2 0%, #6e8a5a 30%, #b23a3e 60%, #a22a34 80%, #b8b8b2 100%); }

  .page-footer { position: absolute; left: 0; top: 927px; width: 773px; height: 73px; background: var(--brand-green); color: var(--paper); }
  .footer-address { position: absolute; left: 49px; top: 13px; font-style: italic; font-weight: 700; font-size: 12.8px; line-height: 19px; }
  .page-number { position: absolute; left: 666px; top: 16px; font-weight: 700; font-size: 15.5px; }
</style>
</head>
<body>
<main class="sheet-board">

  <section class="page page--1">
    <header class="page-header">
      <svg class="header-wave" width="773" height="215" viewBox="0 0 773 215"><path d="M0,0 H773 V166 C700,130 600,104 520,108 C420,114 350,174 230,174 C120,174 50,145 0,124 Z" fill="var(--brand-green)"/></svg>
      <div class="brand-box"><span class="brand-name">FernHollows</span></div>
      <div class="brand-tagline">Landscape and Maintenance, Inc.</div>
      <div class="report-kind">Landscape, Irr. &amp; Property Inspection</div>
    </header>
    <h1 class="property-title">GARDENS ON MILLBROOK POA &amp; RETAIL</h1>
    <p class="report-month">Month of November</p>
    <div class="inspection-table">
      <div class="inspection-row">
        <div class="finding"><h2 class="finding-title">1. Grasses Throughout:</h2><p class="finding-text">Right now the Muhly grass is blooming and looks great. The crew went around and trimmed them all up so they look fresh and clean. There were some of the types that were not blooming, that we trimmed back farther.</p></div>
        <div class="evidence"><div class="photo photo--main tone-grass" role="img" aria-label="Photo of blooming pink Muhly grass bed beside a curb"></div></div>
      </div>
      <div class="inspection-row">
        <div class="finding"><h2 class="finding-title">1. Grasses Throughout:</h2><p class="finding-text">Right now the Muhly grass is blooming and looks great. The crew went around and trimmed them all up so they look fresh and clean. There were some of the types that were not blooming, that we trimmed back farther.</p></div>
        <div class="evidence"><div class="photo photo--main tone-street" role="img" aria-label="Photo of trimmed grass island at a street crosswalk"></div></div>
      </div>
      <div class="inspection-row">
        <div class="finding"><h2 class="finding-title">2. Flowers:</h2><p class="finding-text">Both main entrances are in need of fresh</p></div>
        <div class="evidence"><div class="photo photo--short tone-wall" role="img" aria-label="Photo of planting bed along a building wall"></div></div>
      </div>
    </div>
    <footer class="page-footer">
      <p class="footer-address">Landscape and Grounds Maintenance Division 4120 Alder Creek Lane Pine Hollow,<br>FL 30418 555-014-0250 • Fax 555-014-4069</p>
      <p class="page-number">Page | 1</p>
    </footer>
  </section>

  <section class="page page--2">
    <header class="page-header">
      <svg class="header-wave" width="773" height="215" viewBox="0 0 773 215"><path d="M0,0 H773 V166 C700,130 600,104 520,108 C420,114 350,174 230,174 C120,174 50,145 0,124 Z" fill="var(--brand-green)"/></svg>
      <div class="brand-box"><span class="brand-name">FernHollows</span></div>
      <div class="brand-tagline">Landscape and Maintenance, Inc.</div>
      <div class="report-kind">Landscape, Irr. &amp; Property Inspection</div>
    </header>
    <h1 class="property-title">GARDENS ON MILLBROOK POA &amp; RETAIL</h1>
    <div class="inspection-table">
      <div class="inspection-row">
        <div class="finding"><h2 class="finding-title">3. Palms Need Trimming:</h2><p class="finding-text">All the Palms could use a trimming, there are dead frons and some hanging seed pods and boots. Let us know if and when you would like to get this scheduled.</p></div>
        <div class="evidence"><div class="photo photo--main tone-palm" role="img" aria-label="Photo of tall palms along an entry road"></div></div>
      </div>
      <div class="inspection-row">
        <div class="finding"><h2 class="finding-title">3. Palms Need Trimming:</h2><p class="finding-text">All the Palms could use a trimming, there are dead frons and some hanging seed pods and boots. Let us know if and when you would like to get this scheduled.</p></div>
        <div class="evidence"><div class="photo photo--main tone-palm" role="img" aria-label="Photo of untrimmed palms near a parking lot"></div></div>
      </div>
      <div class="inspection-row">
        <div class="finding"><h2 class="finding-title finding-title--tight">4. Fill In:</h2><p class="finding-text">We should fill this corner in where truck run over the corner with additional plants.</p></div>
        <div class="evidence"><div class="photo photo--main tone-shrub" role="img" aria-label="Photo of a damaged shrub bed corner at a curb"></div></div>
      </div>
    </div>
    <footer class="page-footer">
      <p class="footer-address">Landscape and Grounds Maintenance Division 4120 Alder Creek Lane Pine Hollow,<br>FL 30418 555-014-0250 • Fax 555-014-4069</p>
      <p class="page-number">Page | 2</p>
    </footer>
  </section>

  <section class="page page--3">
    <header class="page-header">
      <svg class="header-wave" width="773" height="215" viewBox="0 0 773 215"><path d="M0,0 H773 V166 C700,130 600,104 520,108 C420,114 350,174 230,174 C120,174 50,145 0,124 Z" fill="var(--brand-green)"/></svg>
      <div class="brand-box"><span class="brand-name">FernHollows</span></div>
      <div class="brand-tagline">Landscape and Maintenance, Inc.</div>
      <div class="report-kind">Landscape, Irr. &amp; Property Inspection</div>
    </header>
    <h1 class="property-title">GARDENS ON MILLBROOK POA...CONT</h1>
    <div class="inspection-table">
      <div class="inspection-row">
        <div class="finding"><h2 class="finding-title">5. Fill in Coonties:</h2><p class="finding-text finding-text--short">Coonties need to be filled in here. As well as side of Burger Den.</p></div>
        <div class="evidence">
          <div class="photo photo--pair-a tone-shrub" role="img" aria-label="Photo of a parking island with a young tree and coonties"></div>
          <div class="photo photo--pair-b tone-wall" role="img" aria-label="Photo of coonties beside a building corner"></div>
        </div>
      </div>
      <div class="inspection-row">
        <div class="finding"><h2 class="finding-title finding-title--tight">6. Mulch:</h2><p class="finding-text">Overall the place could use fresh mulch, or we could just mulch these washed out areas that are an eye sore.</p></div>
        <div class="evidence"><div class="photo photo--narrow tone-wall" role="img" aria-label="Photo of a washed-out mulch bed along a wall"></div></div>
      </div>
      <div class="inspection-row">
        <div class="finding"><h2 class="finding-title finding-title--tight">7. Pruning:</h2><p class="finding-text finding-text--short">All the little palms have been pruned up to look clean</p></div>
        <div class="evidence"><div class="photo photo--narrow tone-wall" role="img" aria-label="Photo of small pruned palms along a storefront"></div></div>
      </div>
    </div>
    <footer class="page-footer">
      <p class="footer-address">Landscape and Grounds Maintenance Division 4120 Alder Creek Lane Pine Hollow,<br>FL 30418 555-014-0250 • Fax 555-014-4069</p>
      <p class="page-number">Page | 3</p>
    </footer>
  </section>

  <section class="page page--4">
    <header class="page-header">
      <svg class="header-wave" width="773" height="215" viewBox="0 0 773 215"><path d="M0,0 H773 V166 C700,130 600,104 520,108 C420,114 350,174 230,174 C120,174 50,145 0,124 Z" fill="var(--brand-green)"/></svg>
      <div class="brand-box"><span class="brand-name">FernHollows</span></div>
      <div class="brand-tagline">Landscape and Maintenance, Inc.</div>
      <div class="report-kind">Landscape, Irr. &amp; Property Inspection</div>
    </header>
    <h1 class="property-title">GARDENS ON MILLBROOK POA...CONT</h1>
    <div class="inspection-table">
      <div class="inspection-row">
        <div class="finding"><h2 class="finding-title">8. Plants filling in:</h2><p class="finding-text">The copper plants and Jasmine are all filling in nicely</p></div>
        <div class="evidence"><div class="photo photo--narrow tone-red" role="img" aria-label="Photo of red copper plants along a sidewalk"></div></div>
      </div>
      <div class="inspection-row">
        <div class="finding"><h2 class="finding-title">8. Plants filling in:</h2><p class="finding-text">The copper plants and Jasmine are all filling in nicely</p></div>
        <div class="evidence"><div class="photo photo--narrow tone-red" role="img" aria-label="Photo of copper plants under a palm by the road"></div></div>
      </div>
      <div class="inspection-row">
        <div class="finding"><h2 class="finding-title">8. Text Title</h2><p class="finding-text">Detail of the information is written in this column</p></div>
        <div class="evidence"><div class="photo photo--narrow tone-shrub" role="img" aria-label="Photo of coonties at a building corner"></div></div>
      </div>
    </div>
    <footer class="page-footer">
      <p class="footer-address">Landscape and Grounds Maintenance Division 4120 Alder Creek Lane Pine Hollow,<br>FL 30418 555-014-0250 • Fax 555-014-4069</p>
      <p class="page-number">Page | 4</p>
    </footer>
  </section>

</main>
</body>
</html>
```